Creative, fresh business card design for Ripplecraft Facades

We need a fresh, creative business card design for Ripplecraft Facades. We are the manufacturer of Ripplecraft Facades in Australia. Wall panels are 2400 x 1200mm panels made from MDF and feature 3D patterns on the face of the panel. The colours to be used are green, silver/grey and white RGB
Red 187
Green 207
Blue 65.

An idea is to possibly use a watermark of one of our designs as a background (like on the "Grids" design on the left hand side of page 2 of our brochure).

Target Market(s)

Interior designers, architects, builders and home renovators

Industry/Entity Type

Business

Contact Information for Business Card

Details to go on the card are:
Our logo (attached),
Slogan: "Decorative panels for interiors and exteriors",
Contact name,
Position,
Mobile phone number,
Business address,
Business phone,
Business fax,
Website and
Email address.

I have attached a few images of our panels and our brochure for reference.

The colours of the business card should feature our logo colours which are: RGB
Red 187
Green 207
Blue 65

Requirements
Must have
• Very modern fonts and design. Some of the designs shown especially the "Prisms" design which is a popular design.
Nice to have
• Creative but simple design. Very contemporary.
Should not have
• Anything ornate or old fashioned.

```html
<!DOCTYPE html>
<html lang="en">
<head>
<meta charset="utf-8">
<title>Ripplecraft Facades – Business Card</title>
<link href="https://fonts.googleapis.com/css2?family=Arimo:wght@400;700&display=swap" rel="stylesheet">
<style>
  :root {
    --brand-green: rgb(187, 207, 65);
    --brand-grey: #8e8f94;
    --strip-grey: #a5a6ab;
    --paper: #ffffff;
    --backdrop: #ececec;
    --photo-red: #c2344f;
    --photo-pink: #e0607a;
    --photo-warm: #d9a15a;
    --photo-deep: #7a1f33;
  }
  * { margin: 0; padding: 0; box-sizing: border-box; }
  html, body {
    width: 1200px; height: 987px; overflow: hidden;
    background: var(--backdrop);
    font-family: "Arimo", Arial, sans-serif;
  }
  .canvas { position: relative; width: 1200px; height: 987px; }

  .card {
    position: absolute; left: 293px; width: 615px; height: 350px;
    overflow: hidden; box-shadow: 0 3px 10px rgba(0,0,0,0.18);
  }
  .card--front { top: 130px; display: flex; background: var(--paper); }
  .card--back { top: 505px; }

  .contact-panel {
    width: 292px; flex: none; height: 100%; background: var(--brand-green);
    color: var(--paper); padding: 78px 0 0 27px; overflow: hidden;
  }
  .contact-name { font-size: 22px; font-weight: 700; letter-spacing: 0.3px; line-height: 1; }
  .contact-role { font-size: 17px; margin-top: 7px; }
  .contact-address { font-size: 17px; line-height: 23px; margin-top: 14px; }
  .contact-list { list-style: none; margin-top: 9px; font-size: 17px; }
  .contact-list li { display: flex; align-items: center; height: 23.5px; white-space: nowrap; }
  .contact-list svg { width: 14px; height: 14px; margin-right: 12px; fill: var(--paper); flex: none; }

  .brand-panel {
    flex: 1; display: flex; flex-direction: column; align-items: center; justify-content: center;
    padding-bottom: 8px;
  }
  .brand-name {
    display: flex; align-items: center; gap: 9px; white-space: nowrap;
    font-size: 24px; font-weight: 700; color: var(--brand-green); letter-spacing: 0.2px;
  }
  .brand-square { width: 16px; height: 16px; background: var(--brand-green); flex: none; }
  .brand-slogan {
    margin-top: 14px; text-align: center; color: var(--brand-grey);
    font-size: 13.5px; letter-spacing: 2.4px; line-height: 16px;
  }
  .side-strip { width: 12px; flex: none; height: 100%; background: var(--strip-grey); }

  .panel-photo {
    position: absolute; inset: 0;
    background:
      linear-gradient(100deg, var(--photo-deep) 0%, var(--photo-red) 25%, var(--photo-pink) 45%, var(--photo-red) 58%, var(--photo-warm) 78%, #5a8c8a 100%);
  }
  .back-brand {
    position: absolute; left: 39px; top: 186px; color: var(--paper);
  }
  .back-brand .brand-name { color: var(--paper); font-size: 24px; }
  .back-brand .brand-square { background: var(--paper); }
  .back-brand .brand-slogan { color: var(--paper); text-align: left; font-size: 12.5px; margin-top: 12px; }
</style>
</head>
<body>
<main class="canvas">
  <section class="card card--front">
    <div class="contact-panel">
      <h1 class="contact-name">DANIEL MARSH</h1>
      <p class="contact-role">CEO&amp;Founder</p>
      <p class="contact-address">412 Harbour Street<br>Geelong, Victoria 3220</p>
      <ul class="contact-list">
        <li><svg viewBox="0 0 16 16"><path d="M3.6 1l2.6 3-1.5 1.8c.9 2 2.5 3.6 4.5 4.5L11 8.8l3 2.6-1.4 2.9C7 14 2 9 1.7 2.4z"/></svg>(555) 210-4471</li>
        <li><svg viewBox="0 0 16 16"><path d="M4 1h7l1 1v3H4zM1 6h14v6h-3v3H4v-3H1zm4 4v4h6v-4z"/></svg>(555) 210-4472</li>
        <li><svg viewBox="0 0 16 16"><path d="M1 3h14v10H1zm1.5 1.3V5l5.5 4 5.5-4v-.7L8 8.2z"/></svg>dmarsh@ripplecraft.com</li>
        <li><svg viewBox="0 0 16 16"><path d="M8 1a7 7 0 110 14A7 7 0 018 1zm0 1.5C6.8 3.8 6.2 5.8 6.1 7.3h3.8C9.8 5.8 9.2 3.8 8 2.5zM2.6 8.7c.3 2.3 1.9 4.1 4 4.6C5.5 12 4.8 10.3 4.7 8.7zm8.7 0c-.1 1.6-.8 3.3-1.9 4.6 2.1-.5 3.7-2.3 4-4.6z"/></svg>www.ripplecraft.com</li>
      </ul>
    </div>
    <div class="brand-panel">
      <div class="brand-name"><span class="brand-square"></span>Ripplecraft Facades</div>
      <p class="brand-slogan">decorative panels for<br>interiors &amp; landscapes</p>
    </div>
    <div class="side-strip"></div>
  </section>

  <section class="card card--back">
    <div class="panel-photo" role="img" aria-label="Interior with a red pyramid-textured wall panel, hanging amber lamps and glass shelves holding coloured vases"></div>
    <div class="back-brand">
      <div class="brand-name"><span class="brand-square"></span>Ripplecraft Facades</div>
      <p class="brand-slogan">decorative panels for<br>interiors &amp; landscapes</p>
    </div>
  </section>
</main>
</body>
</html>
```